Business Cards for a law firm

Business cards for our law firm. Use our silhoette logo and OAK PARTNERS - check our website (www.oakpartners.example)

Contact Information for Business Card

our silhouette logo, OAK PARTNERS, 800-555-0147, Dorian Pemberton, dorian@oakpartners.example

Requirements
Must have
• our silhouette logo, OAK PARTNERS, 800-555-0147, Dorian Pemberton, dorian@oakpartners.example

```html
<!DOCTYPE html>
<html lang="en">
<head>
<meta charset="utf-8">
<title>Oak Partners – Business Cards</title>
<link rel="stylesheet" href="https://fonts.googleapis.com/css2?family=Montserrat:wght@700&family=Roboto:wght@400&display=swap">
<style>
  :root {
    --stage: #1f2024;
    --navy: #16246e;
    --navy-deep: #0f1a5c;
    --blue-mid: #1d2f8f;
    --blue-light: #4c6cc4;
    --paper: #ffffff;
    --ghost: #eceef3;
    --ink-grey: #555a63;
    --edge: #3a56a8;
  }
  * { margin: 0; padding: 0; box-sizing: border-box; }
  html, body { width: 1200px; height: 840px; overflow: hidden; }
  body {
    background: var(--stage);
    display: flex;
    align-items: center;
    justify-content: center;
    gap: 40px;
  }
  .card {
    position: relative;
    width: 540px;
    height: 309px;
    border-radius: 22px;
    overflow: hidden;
  }

  /* Back side */
  .card--back { background: var(--navy-deep); }
  .back-pattern {
    position: absolute;
    inset: 0;
    background: linear-gradient(125deg, var(--navy-deep) 0%, var(--blue-mid) 50%, var(--blue-light) 100%);
  }
  .back-brand {
    position: absolute;
    left: 0; right: 0; top: 50%;
    transform: translateY(-50%);
    display: flex;
    align-items: center;
    justify-content: center;
    gap: 14px;
  }
  .back-brand .brand-mark { width: 26px; height: 26px; background: var(--paper); }
  .back-brand .brand-name {
    font-family: "Montserrat", sans-serif;
    font-weight: 700;
    font-size: 30px;
    letter-spacing: 2px;
    color: var(--paper);
  }

  /* Front side */
  .card--front {
    background: var(--paper);
    border-bottom: 3px solid var(--edge);
  }
  .corner-tab {
    position: absolute;
    top: 14px; right: 0;
    width: 12px; height: 24px;
    background: var(--navy);
  }
  .ghost-figure {
    position: absolute;
    right: 20px; top: 55px;
    width: 170px; height: 254px;
    background: linear-gradient(180deg, var(--ghost) 0%, #f4f5f8 100%);
    border-radius: 60px 60px 0 0;
  }
  .holder-name {
    position: absolute;
    top: 30px; right: 36px;
    font-family: "Montserrat", sans-serif;
    font-weight: 700;
    font-size: 19px;
    letter-spacing: 1.5px;
    color: var(--navy);
  }
  .front-brand {
    position: absolute;
    left: 40px; top: 158px;
    display: flex;
    align-items: center;
    gap: 14px;
  }
  .front-brand .brand-mark { width: 34px; height: 34px; background: var(--navy); }
  .front-brand .brand-name {
    font-family: "Montserrat", sans-serif;
    font-weight: 700;
    font-size: 33px;
    letter-spacing: 1.5px;
    color: var(--navy);
  }
  .contact-list {
    position: absolute;
    left: 88px; top: 208px;
    list-style: none;
    font-family: "Roboto", sans-serif;
    font-size: 16px;
    color: var(--ink-grey);
  }
  .contact-list li {
    display: flex;
    align-items: center;
    gap: 9px;
    height: 25px;
  }
  .contact-list svg { width: 14px; height: 14px; fill: var(--navy); flex: none; }
</style>
</head>
<body>

  <section class="card card--back" aria-label="Card back">
    <div class="back-pattern" role="img" aria-label="Repeating pattern of standing figure silhouettes in shades of blue"></div>
    <div class="back-brand">
      <span class="brand-mark"></span>
      <span class="brand-name">OAK PARTNERS</span>
    </div>
  </section>

  <section class="card card--front" aria-label="Card front">
    <span class="corner-tab"></span>
    <div class="ghost-figure" role="img" aria-label="Large faint decorative figure area in pale grey"></div>
    <h1 class="holder-name">DORIAN PEMBERTON</h1>
    <div class="front-brand">
      <span class="brand-mark"></span>
      <span class="brand-name">OAK PARTNERS</span>
    </div>
    <ul class="contact-list">
      <li>
        <svg viewBox="0 0 16 16" aria-hidden="true"><path d="M3 1h3l1.5 4-2 1.3a9 9 0 0 0 4.2 4.2L11 8.5l4 1.5v3a2 2 0 0 1-2 2A12 12 0 0 1 1 3a2 2 0 0 1 2-2z"/></svg>
        800-555-0147
      </li>
      <li>
        <svg viewBox="0 0 16 16" aria-hidden="true"><path d="M1 3h14v10H1z M2 4l6 5 6-5" fill="none" stroke="#16246e" stroke-width="1.6"/></svg>
        dorian@oakpartners.example
      </li>
      <li>
        <svg viewBox="0 0 16 16" aria-hidden="true"><circle cx="8" cy="8" r="7"/><path d="M1 8h14M8 1c-3 3-3 11 0 14M8 1c3 3 3 11 0 14" fill="none" stroke="#fff" stroke-width="1"/></svg>
        www.oakpartners.example
      </li>
    </ul>
  </section>

</body>
</html>
```